Lifestyle Coaching comp needs wordpress design. We focus on strong mindsets, fitness and nutrition

BrenVigor Lifestyle Coaching needs a wordpress site. Our tagline for now (may change) is Mindset Mastery.Fitness Badassery. Sustainable Nutrition
Our logo is below. Would like to see some complimentary colors to liven it up. Clients need to come to site and get immediate professional, but fun feel. They need to have the impression that we are the last destination in their journey to wellness. Blogging, workout videos, pictures

Target Market(s)

Mostly women ages 20+

Industry/Entity Type

Nutrition

Colors
33a6d7
86cae7
ceeaf6
cfdeed
5c5c5c
cbcbcb
474747

Requirements
Must have
• A strong, badass feel :) While not being intimidating
Nice to have
• Fun fonts. Love the font in my logo
Should not have
• Pics, logos of flowers, heads, fruit.

```html
<!DOCTYPE html>
<html lang="en">
<head>
<meta charset="utf-8">
<title>BrenVigor Lifestyle Coaching</title>
<link href="https://fonts.googleapis.com/css2?family=Raleway:wght@400;500;600&family=Open+Sans:wght@400;600&display=swap" rel="stylesheet">
<style>
:root{
  --blue:#33a6d7;
  --blue-mid:#86cae7;
  --blue-soft:#ceeaf6;
  --ink:#2b2b2b;
  --text:#5c5c5c;
  --grey:#cbcbcb;
  --band:#e9e9e9;
  --footer:#3d3d3d;
  --white:#ffffff;
}
*{margin:0;padding:0;box-sizing:border-box}
html,body{width:751px;height:1200px;overflow:hidden;background:var(--white)}
body{position:relative;font-family:"Open Sans",Arial,sans-serif;color:var(--text)}
.abs{position:absolute}

/* header */
.site-header{left:0;top:0;width:751px;height:67px;background:var(--white)}
.brand{left:90px;top:20px;display:flex;align-items:center;gap:7px}
.brand-dot{width:18px;height:18px;border-radius:50%;background:var(--blue)}
.brand-name{font-family:"Raleway",sans-serif;font-weight:600;font-size:22px;color:var(--blue);letter-spacing:.5px}
.main-nav{top:29px;left:276px;display:flex;gap:0;font-family:"Raleway",sans-serif;font-weight:500;font-size:9.5px;color:var(--ink)}
.main-nav span{position:absolute;white-space:nowrap}

/* hero */
.hero{left:0;top:67px;width:751px;height:303px;background:linear-gradient(100deg,#5a4c44 0%,#8b7a6d 35%,#a59a90 55%,#6d6660 80%,#4a4643 100%)}
.hero-caption{left:169px;top:169px;width:417px;height:76px;border:1px solid rgba(255,255,255,.8);background:rgba(40,40,40,.45);color:var(--white);font-family:"Raleway",sans-serif;font-weight:500;font-size:22px;line-height:26px;text-align:center;padding-top:12px}
.hero-dots{left:359px;top:352px;display:flex;gap:3px}
.hero-dots i{width:9px;height:9px;border-radius:50%;border:1.5px solid var(--white)}
.hero-dots i.on{background:var(--white)}

/* features */
.features{left:0;top:370px;width:751px;height:174px;background:var(--blue)}
.feature{top:0;width:143px;height:174px;text-align:center;color:var(--white)}
.feature + .feature{border-left:1px solid rgba(255,255,255,.25)}
.feature-ring{position:absolute;left:39px;top:25px;width:65px;height:65px;border-radius:50%;border:2px solid rgba(255,255,255,.85)}
.feature-icon{position:absolute;left:18px;top:18px;width:26px;height:26px;border-radius:50%;background:rgba(255,255,255,.55)}
.feature h3{position:absolute;left:0;top:97px;width:100%;font-family:"Raleway",sans-serif;font-weight:500;font-size:12.5px}
.feature p{position:absolute;left:8px;top:117px;width:127px;font-size:6.4px;line-height:9.6px;color:rgba(255,255,255,.85)}

/* welcome */
.welcome{left:0;top:544px;width:751px;height:167px;text-align:center}
.welcome h1{position:absolute;top:30px;width:100%;font-family:"Raleway",sans-serif;font-weight:400;font-size:17.5px;color:var(--ink)}
.welcome .lead{position:absolute;top:57px;width:100%;font-size:7.4px}
.welcome .body{position:absolute;top:71px;left:120px;width:511px;font-size:6.4px;line-height:12px}
.welcome .body2{position:absolute;top:98px;width:100%;font-size:6.4px}
.btn{position:absolute;left:338px;top:120px;width:71px;height:18px;background:linear-gradient(var(--blue-mid),var(--blue));color:var(--white);font-size:6.8px;line-height:18px;border-radius:2px}

/* blog */
.blog{left:0;top:711px;width:751px;height:210px;background:var(--band);border-top:1px solid var(--grey);border-bottom:1px solid var(--grey)}
.section-title{font-family:"Raleway",sans-serif;font-weight:400;font-size:14.5px}
.blog .section-title{left:95px;top:25px;color:var(--blue)}
.post{top:49px;width:133px}
.post-photo{width:133px;height:70px}
.post h4{margin-top:8px;font-family:"Raleway",sans-serif;font-weight:600;font-size:8px;color:var(--ink)}
.post p{margin-top:4px;font-size:6.2px;line-height:12px;color:var(--text)}

/* media */
.gallery-title{left:87px;top:948px;color:var(--ink)}
.video-title{left:384px;top:948px;color:var(--blue)}
.thumb{width:87px;height:58px;border:1px solid var(--grey)}
.play{position:absolute;left:34px;top:20px;width:18px;height:18px;border-radius:50%;background:var(--white)}
.play::after{content:"";position:absolute;left:7px;top:5px;border-left:6px solid #222;border-top:4px solid transparent;border-bottom:4px solid transparent}

/* footer */
.site-footer{left:0;top:1140px;width:751px;height:60px;background:var(--footer)}
.footer-nav{left:87px;top:16px;font-family:"Raleway",sans-serif;font-weight:600;font-size:7.4px;color:var(--white);word-spacing:1px}
.copyright{left:87px;top:32px;font-size:6.2px;color:#9a9a9a}
.social{top:17px;width:12px;height:12px;border-radius:2px;background:var(--white)}
</style>
</head>
<body>

<header class="site-header abs">
  <div class="brand abs"><span class="brand-dot"></span><span class="brand-name">BrenVigor</span></div>
  <nav class="main-nav abs">
    <span style="left:0">HOME</span>
    <span style="left:50px">ABOUT US</span>
    <span style="left:119px">SERVICES</span>
    <span style="left:185px">PHOTOS</span>
    <span style="left:244px">VIDEO</span>
    <span style="left:294px">BLOG</span>
    <span style="left:341px">CONTACT</span>
  </nav>
</header>

<section class="hero abs" role="img" aria-label="Coach encouraging a woman doing sit-ups in a brick-walled gym">
</section>
<div class="hero-caption abs">Mindset Mastery.Fitness Badassery.<br>Sustainable Nutrition</div>
<div class="hero-dots abs"><i class="on"></i><i></i><i></i></div>

<section class="features abs">
  <div class="feature abs" style="left:87px">
    <div class="feature-ring"><div class="feature-icon" role="img" aria-label="Mindset icon"></div></div>
    <h3>Strong Mindsets</h3>
    <p>Curabitur iaculis tempus eros vel mi sit amet magna malesuada ultrices Ut nisi erat fermentum</p>
  </div>
  <div class="feature abs" style="left:231px">
    <div class="feature-ring"><div class="feature-icon" role="img" aria-label="Fitness icon"></div></div>
    <h3>Fitness</h3>
    <p>Curabitur iaculis tempus eros vel mi sit amet magna malesuada ultrices Ut nisi erat fermentum</p>
  </div>
  <div class="feature abs" style="left:374px">
    <div class="feature-ring"><div class="feature-icon" role="img" aria-label="Nutrition icon"></div></div>
    <h3>Nutritions</h3>
    <p>Curabitur iaculis tempus eros vel mi sit amet magna malesuada ultrices Ut nisi erat fermentum</p>
  </div>
  <div class="feature abs" style="left:517px">
    <div class="feature-ring">
      <svg width="61" height="61" viewBox="0 0 61 61"><circle cx="30.5" cy="30.5" r="16" fill="#fff"/><path d="M23 31l5 5 10-11" fill="none" stroke="#33a6d7" stroke-width="4" stroke-linecap="round" stroke-linejoin="round"/></svg>
    </div>
    <h3>Join Us Now</h3>
    <p>Curabitur iaculis tempus eros vel mi sit amet magna malesuada ultrices Ut nisi erat fermentum vel con</p>
  </div>
</section>

<section class="welcome abs">
  <h1>Welcome to BrenVigor Website Mainpage</h1>
  <p class="lead">Praesent elementum elit at tellus nec ultricies sit amet porttitor mattis enim In massa libero interdum nec interdum vel blandit sed nulla</p>
  <p class="body">Vivamus porttitor purus nisi eleifend libero a tempus libero lectus feugiat felis Morbi diam mauris viverra in gravida eu mattis in ante Morbi eget arcu Morbi porta libero id ullamcorper nonummy nibh ligula pulvinar metus eget consectetuer augue nisi quis lacus</p>
  <p class="body2">Ut ac mi quis lacus mollis aliquam Curabitur iaculis tempus eros Curabitur vel mi sit amet magna malesuada ultrices Ut nisi erat fermentum vel congue</p>
  <span class="btn">READ MORE</span>
</section>

<section class="blog abs">
  <h2 class="section-title abs">Recent Blog Post</h2>
  <article class="post abs" style="left:95px">
    <div class="post-photo" role="img" aria-label="Women stretching in a fitness class" style="background:linear-gradient(#c9c3c0,#e26a8e)"></div>
    <h4>Morbi diam mauris viverra</h4>
    <p>in gravida eu mattis in ante Morbi eget arcu Morbi porta libero id ullamcorper nonummy nibh ligula pulvinar</p>
  </article>
  <article class="post abs" style="left:237px">
    <div class="post-photo" role="img" aria-label="Woman stretching arms against a pastel sky" style="background:linear-gradient(120deg,#9ec8e8,#e8b4cf)"></div>
    <h4>Morbi diam mauris viverra</h4>
    <p>in gravida eu mattis in ante Morbi eget arcu Morbi porta libero id ullamcorper nonummy nibh ligula pulvinar</p>
  </article>
  <article class="post abs" style="left:380px">
    <div class="post-photo" role="img" aria-label="Woman jogging outdoors with earphones" style="background:linear-gradient(90deg,#6e8a4a,#b8cf7a)"></div>
    <h4>Morbi diam mauris viverra</h4>
    <p>in gravida eu mattis in ante Morbi eget arcu Morbi porta libero id ullamcorper nonummy nibh ligula pulvinar</p>
  </article>
  <article class="post abs" style="left:521px">
    <div class="post-photo" role="img" aria-label="Woman doing push-ups in a gym" style="background:linear-gradient(90deg,#8e8a88,#4a4a4c)"></div>
    <h4>Morbi diam mauris viverra</h4>
    <p>in gravida eu mattis in ante Morbi eget arcu Morbi porta libero id ullamcorper nonummy nibh ligula pulvinar</p>
  </article>
</section>

<h2 class="section-title gallery-title abs">Photo Gallery</h2>
<div class="thumb abs" style="left:88px;top:975px;background:linear-gradient(#a9c86a,#6d8f3f)" role="img" aria-label="Seniors walking in a park"></div>
<div class="thumb abs" style="left:181px;top:975px;background:linear-gradient(#2a8fd0,#1b6aa8)" role="img" aria-label="Woman stretching under a blue sky"></div>
<div class="thumb abs" style="left:274px;top:975px;background:linear-gradient(#c89a6a,#4a3a30)" role="img" aria-label="Man resting on steps at sunset"></div>
<div class="thumb abs" style="left:88px;top:1040px;background:linear-gradient(#8aa46a,#3c3c38)" role="img" aria-label="Group doing tai chi outdoors"></div>
<div class="thumb abs" style="left:181px;top:1040px;background:linear-gradient(#e0dcd4,#a08070)" role="img" aria-label="Woman sitting cross-legged on a mat"></div>
<div class="thumb abs" style="left:274px;top:1040px;background:linear-gradient(#e8e8e8,#6a6060)" role="img" aria-label="Woman lacing training shoes"></div>

<h2 class="section-title video-title abs">Watch Video</h2>
<div class="thumb abs" style="left:386px;top:975px;background:linear-gradient(#8a6a5a,#3a3a3a)" role="img" aria-label="Video: runners training together"><span class="play"></span></div>
<div class="thumb abs" style="left:481px;top:975px;background:linear-gradient(#9a7a66,#2e2e36)" role="img" aria-label="Video: woman lifting weights"><span class="play"></span></div>
<div class="thumb abs" style="left:576px;top:975px;background:linear-gradient(#5a5a5a,#1e1e1e)" role="img" aria-label="Video: push-up workout"><span class="play"></span></div>
<div class="thumb abs" style="left:386px;top:1040px;background:linear-gradient(#9a9a9a,#4a4a4a)" role="img" aria-label="Video: treadmill session"><span class="play"></span></div>
<div class="thumb abs" style="left:481px;top:1040px;background:linear-gradient(#e0a050,#4a3a3a)" role="img" aria-label="Video: mountain hike at sunrise"><span class="play"></span></div>
<div class="thumb abs" style="left:576px;top:1040px;background:linear-gradient(#2a6ab0,#123a70)" role="img" aria-label="Video: runner with heart-rate graphic"><span class="play"></span></div>

<footer class="site-footer abs">
  <p class="footer-nav abs">HOME | ABOUT US | SERVICES | PHOTOS | VIDEO | BLOG | CONTACT</p>
  <p class="copyright abs">© 2015 Company Name  All right reserved  Term of Use</p>
  <span class="social abs" style="left:615px"></span>
  <span class="social abs" style="left:631px"></span>
  <span class="social abs" style="left:647px"></span>
</footer>

</body>
</html>
```